Flyer for Commercial Roofing Company

We are seeking a talented graphic designer to create a high-quality, visually appealing bifold brochure for Brackenvale Roofing, a certified commercial roofing company specializing in apartment communities. The brochure will be 8.5x11 inches when folded and 17x11 inches when open, containing a front cover, two inside pages, and a back cover. The content is already developed, highlighting our services, key features, and contact information. The design should incorporate professional imagery of multifamily properties, modern icons, a clean layout, and our brand colors and logo to convey trust, expertise, and innovation. The goal is to produce a compelling marketing piece that engages property managers and decision-makers.
Target Market(s)
Apartment Communites
Look and feel
Each slider illustrates characteristics of the customer's brand and the style your logo design should communicate.

```html
<!DOCTYPE html>
<html lang="en">
<head>
<meta charset="utf-8">
<title>Brackenvale Roofing – Bifold Brochure</title>
<link href="https://fonts.googleapis.com/css2?family=Montserrat:wght@400;500;600;700;800&display=swap" rel="stylesheet">
<style>
:root{
  --stage:#565656;
  --navy:#2a3795;
  --royal:#2f44b0;
  --bright:#1f62d8;
  --sky:#5cc4f2;
  --red:#a31d24;
  --ink:#2b2b2b;
  --mist:#eef0f5;
  --frame:#c9cde8;
  --white:#ffffff;
}
*{box-sizing:border-box;margin:0;padding:0}
html,body{width:1200px;height:2498px;overflow:hidden;background:var(--stage);font-family:"Montserrat",Arial,sans-serif;color:var(--ink)}
.canvas{position:relative;width:1200px;height:2498px}
.label{position:absolute;color:#fff;font-weight:600;font-size:18px;letter-spacing:.5px;text-align:center;width:570px}
.spread{position:absolute;left:30px;width:1140px;height:735px;box-shadow:0 6px 20px rgba(0,0,0,.35)}
.page{position:absolute;top:0;width:570px;height:735px;overflow:hidden}
.page--left{left:0}.page--right{left:570px}
.abs{position:absolute}
.photo{position:absolute}
.bg{position:absolute;inset:0}

/* back cover */
.back{background:var(--white)}
.quote-tag{left:248px;top:44px;width:300px;height:26px;background:linear-gradient(90deg,var(--navy) 70%,rgba(42,55,149,0));color:#fff;font-weight:700;font-size:18px;padding:2px 12px}
.quote{left:250px;top:84px;width:300px;font-size:16px;line-height:20px;color:var(--ink)}
.quote-by{right:40px;top:155px;font-size:10px;color:var(--red);font-weight:600}
.frame{background:#fff;border:9px solid var(--frame);box-shadow:0 4px 12px rgba(0,0,0,.15)}
.frame .inner{position:absolute;inset:3px;border:6px solid var(--navy)}
.cta{left:142px;top:453px;width:286px;height:64px;background:var(--red);color:#fff;text-align:center;outline:2px solid var(--red);outline-offset:3px}
.cta .small{display:block;color:#f4c84a;font-size:14px;margin-top:12px}
.cta .big{display:block;font-weight:700;font-size:14px}
.contact{left:209px;top:537px;width:361px;height:198px;background:linear-gradient(135deg,var(--navy),var(--royal));color:#fff;padding:24px 24px}
.contact h3{font-size:17px;font-weight:700}
.contact p{font-size:10px;margin-top:1px}
.contact .btn{display:inline-block;background:#fff;color:var(--red);font-size:10px;font-weight:600;padding:3px 6px;margin:10px 0 14px}
.contact li{list-style:none;font-size:11px;display:flex;align-items:center;gap:12px;margin-bottom:5px}
.contact li svg{width:14px;height:14px}

/* front cover */
.front{background:linear-gradient(160deg,var(--royal),var(--navy) 60%,#2540a8)}
.brand{left:0;width:570px;top:110px;text-align:center;color:#fff;font-weight:800;font-size:26px;line-height:30px;letter-spacing:1px}
.brand .mark{display:inline-block;width:14px;height:14px;background:#fff;margin-bottom:14px}
.kicker{left:28px;top:248px;color:var(--sky);font-size:21px;line-height:22px;font-weight:500}
.headline{left:28px;top:300px;color:#fff;font-size:44px;line-height:43px;font-weight:800}
.rule{left:0;top:410px;width:305px;height:3px;background:var(--bright)}
.bullets{left:0;top:420px;width:450px;height:90px;background:var(--red);color:#fff;padding:10px 26px;font-size:16px;font-weight:500;line-height:24px;list-style:none}
.bullets b{font-weight:700}
.bullets li::before{content:"★";margin-right:14px;font-size:12px}
.bullets-line{left:130px;top:420px;width:330px;height:96px;border-right:2px solid #fff;border-bottom:2px solid #fff}
.partner{left:373px;top:570px;color:#fff}
.partner .t1{font-size:15px;line-height:16px}
.partner .t2{font-size:23px;line-height:24px;font-weight:800;margin-top:4px}
.partner .url{font-size:11px;margin-top:26px}

/* inside 1 */
.in1{background:var(--white)}
.why{left:25px;top:26px;font-size:22px;line-height:23px;font-weight:800;color:var(--red)}
.why span{color:var(--navy)}
.lead{left:25px;top:80px;width:470px;font-size:12px;line-height:17px}
.band{left:0;top:160px;width:457px;height:210px;background:linear-gradient(90deg,var(--royal),var(--navy))}
.feats{left:25px;top:195px;color:#fff;list-style:none}
.feats li{margin-bottom:14px;font-size:12px;font-weight:700}
.feats li::before{content:"★";font-size:10px;margin-right:10px}
.feats small{display:block;font-weight:400;font-size:10px;margin-left:20px;opacity:.9}
.sec-tag{background:var(--red);color:#fff;font-weight:700;font-size:21px;padding:2px 16px;height:34px}
.sec-rule{height:2px;background:var(--navy)}
.item{position:absolute;display:flex;gap:12px;width:260px}
.icon{flex:0 0 58px;height:58px;border:2px solid var(--navy);display:flex;align-items:center;justify-content:center;background:#fff}
.icon svg{width:34px;height:34px;stroke:var(--red);fill:none;stroke-width:2}
.item h4{color:var(--red);font-size:14px;font-weight:700;line-height:16px}
.item p{font-size:12px;line-height:15px;margin-top:2px}
.divider{position:absolute;height:1px;background:#9aa0c8}

/* inside 2 */
.in2{background:var(--white)}
.services-intro{left:25px;top:80px;width:380px;color:#fff;font-size:12px;line-height:16px}
.url-foot{right:26px;bottom:24px;font-size:10px;color:#fff}
</style>
</head>
<body>
<div class="canvas">

  <div class="label" style="left:30px;top:430px">BACK</div>
  <div class="label" style="left:600px;top:430px">FRONT</div>

  <section class="spread" style="top:470px">
    <!-- back cover -->
    <div class="page page--left back">
      <svg class="bg" width="570" height="735" viewBox="0 0 570 735">
        <defs>
          <linearGradient id="backBlue" x1="0" y1="0" x2="1" y2="1">
            <stop offset="0" stop-color="#2f44b0"/><stop offset="1" stop-color="#1f62d8"/>
          </linearGradient>
        </defs>
        <polygon points="0,0 80,0 240,190 105,190 105,540 0,640" fill="url(#backBlue)"/>
        <polygon points="500,190 570,130 570,170 530,215" fill="#eceef4"/>
        <polygon points="40,580 140,520 140,735 40,735" fill="#eceef4"/>
        <polygon points="150,600 210,630 210,735 150,735" fill="#f2f3f7"/>
        <line x1="180" y1="45" x2="210" y2="75" stroke="#2a3795" stroke-width="1.5"/>
        <line x1="190" y1="40" x2="220" y2="70" stroke="#2a3795" stroke-width="1.5"/>
        <polyline points="495,310 495,467 430,467" fill="none" stroke="#a31d24" stroke-width="1.5"/>
      </svg>
      <div class="abs quote-tag">What Our Clients Say:</div>
      <p class="abs quote">Brackenvale Roofing’s expertise and professionalism made all the difference for our property.</p>
      <p class="abs quote-by">– Dana R., Property Manager</p>
      <div class="abs frame" style="left:95px;top:190px;width:375px;height:255px">
        <div class="inner">
          <div class="photo" role="img" aria-label="Roofing contractors in hard hats shaking hands over plans on a rooftop" style="inset:0;background:linear-gradient(180deg,#cfd9e6,#9aa7b5 55%,#e6e2d6)"></div>
        </div>
      </div>
      <div class="abs cta"><span class="small">—— REQUEST A FREE ——</span><span class="big">ROOF INSPECTION TODAY</span></div>
      <div class="abs contact">
        <h3>Get in Touch</h3>
        <p>Ready to protect your property with the best in roofing?</p>
        <span class="btn">Contact us Today!</span>
        <ul>
          <li><svg viewBox="0 0 24 24" fill="#fff"><path d="M6 2l4 4-2 3c1 3 4 6 7 7l3-2 4 4-3 4C10 22 2 14 2 5z"/></svg>555.014.2270</li>
          <li><svg viewBox="0 0 24 24" fill="none" stroke="#fff" stroke-width="2"><rect x="2" y="5" width="20" height="14"/><path d="M2 5l10 8 10-8"/></svg>sales@brackenvaleroofing.com</li>
          <li><svg viewBox="0 0 24 24" fill="none" stroke="#fff" stroke-width="2"><circle cx="12" cy="12" r="10"/><path d="M2 12h20M12 2c4 4 4 16 0 20M12 2c-4 4-4 16 0 20"/></svg>www.brackenvaleroofing.com</li>
        </ul>
      </div>
    </div>

    <!-- front cover -->
    <div class="page page--right front">
      <svg class="bg" width="570" height="735" viewBox="0 0 570 735">
        <polygon points="380,0 570,0 570,210" fill="#2f52c8" opacity=".5"/>
        <polygon points="470,330 570,240 570,420" fill="#1f62d8" opacity=".45"/>
        <circle cx="100" cy="168" r="10" fill="none" stroke="#fff" stroke-width="1"/>
        <circle cx="136" cy="180" r="4" fill="none" stroke="#fff" stroke-width="1"/>
        <circle cx="240" cy="0" r="28" fill="none" stroke="#fff" stroke-width="1" opacity=".5"/>
        <line x1="30" y1="80" x2="65" y2="115" stroke="#fff" stroke-width="1.2" opacity=".7"/>
        <line x1="40" y1="75" x2="75" y2="110" stroke="#fff" stroke-width="1.2" opacity=".7"/>
        <line x1="405" y1="270" x2="440" y2="240" stroke="#fff" stroke-width="1.2" opacity=".7"/>
        <line x1="412" y1="278" x2="447" y2="248" stroke="#fff" stroke-width="1.2" opacity=".7"/>
      </svg>
      <div class="abs brand"><span class="mark"></span><br>BRACKENVALE<br>ROOFING</div>
      <p class="abs kicker">PROTECTING APARTMENT<br>COMMUNITIES WITH</p>
      <h1 class="abs headline">PRECISION ROOFING<br>SOLUTIONS</h1>
      <div class="abs rule"></div>
      <div class="abs bullets-line"></div>
      <ul class="abs bullets">
        <li>CERTIFIED <b>EXPERTISE</b></li>
        <li>UNMATCHED <b>RELIABILITY</b></li>
        <li>INDUSTRY-LEADING <b>WARRANTY</b></li>
      </ul>
      <div class="photo" role="img" aria-label="Two-storey multifamily home with solar panels on a grey roof" style="left:0;top:537px;width:360px;height:198px;background:linear-gradient(180deg,#c8d6e2,#8c939a 45%,#6f7a6a 75%,#b9b5ae)"></div>
      <div class="abs partner">
        <p class="t1">YOUR TRUSTED<br>PARTNER FOR</p>
        <p class="t2">BRACKENVALE<br>ROOFING</p>
        <p class="url">www.brackenvaleroofing.com</p>
      </div>
    </div>
  </section>

  <div class="label" style="left:30px;top:1270px">INSIDE PAGE 1</div>
  <div class="label" style="left:600px;top:1270px">INSIDE PAGE 2</div>

  <section class="spread" style="top:1310px">
    <!-- inside page 1 -->
    <div class="page page--left in1">
      <div class="photo" role="img" aria-label="Faded view of roofers working on a shingled roof" style="left:330px;top:0;width:240px;height:160px;background:linear-gradient(135deg,rgba(255,255,255,0),#dfe2ea)"></div>
      <h2 class="abs why">WHY CHOOSE<br><span>BRACKENVALE ROOFING?</span></h2>
      <p class="abs lead">We specialize in delivering superior roofing services tailored to meet the needs of apartment communities. Our certified experts ensure your property’s roof is built to last.</p>
      <div class="abs band"></div>
      <ul class="abs feats">
        <li>Certified Roofing Contractor:<small>Expert craftsmanship guaranteed.</small></li>
        <li>20-Year NDL Warranty:<small>Peace of mind with long-term protection.</small></li>
        <li>Vendor Credentialing Compliance:<small>Approved with all major platforms.</small></li>
      </ul>
      <div class="abs frame" style="left:295px;top:175px;width:250px;height:170px">
        <div class="inner">
          <div class="photo" role="img" aria-label="Aerial view of a large grey-roofed residence among trees" style="inset:0;background:linear-gradient(180deg,#5f8a4e,#8d96a3 55%,#6b7d55)"></div>
        </div>
      </div>
      <div class="abs sec-tag" style="left:25px;top:400px">OUR ROOFING SOLUTIONS</div>
      <div class="abs sec-rule" style="left:25px;top:434px;width:520px"></div>

      <div class="item" style="left:25px;top:450px">
        <div class="icon"><svg viewBox="0 0 34 34"><path d="M5 30V12h24v18M5 18h24M5 24h24M13 12v18M21 12v18M10 12V6h14v6"/></svg></div>
        <div><h4>TPO Roofing:</h4><p>Energy-efficient and durable for large flat roofs.</p></div>
      </div>
      <div class="divider" style="left:25px;top:518px;width:260px"></div>
      <div class="item" style="left:25px;top:530px">
        <div class="icon"><svg viewBox="0 0 34 34"><rect x="6" y="6" width="16" height="22"/><path d="M9 12h10M9 17h10M9 22h10"/><circle cx="26" cy="24" r="4"/><path d="M26 8v12"/></svg></div>
        <div><h4>EPDM Roofing:</h4><p>Resilient against extreme weather with proven longevity.</p></div>
      </div>
      <div class="divider" style="left:25px;top:598px;width:260px"></div>
      <div class="item" style="left:25px;top:612px">
        <div class="icon"><svg viewBox="0 0 34 34"><path d="M4 18l14-10 12 8-14 10z"/><path d="M9 15l12 8M13 12l12 8"/></svg></div>
        <div><h4>PVC Roofing:</h4><p>Fire, chemical, and water-resistant for multifamily properties.</p></div>
      </div>

      <div class="item" style="left:300px;top:450px;width:250px">
        <div class="icon"><svg viewBox="0 0 34 34"><path d="M4 24L10 10h14l6 14z"/><path d="M8 17h18M6 21h22M14 10l-3 14M20 10l3 14"/></svg></div>
        <div><h4>Asphalt Shingles:</h4><p>Versatile and cost-effective with curb appeal.</p></div>
      </div>
      <div class="divider" style="left:300px;top:518px;width:245px"></div>
      <div class="item" style="left:300px;top:530px;width:250px">
        <div class="icon"><svg viewBox="0 0 34 34"><path d="M4 8h18v8H4zM22 12h6v8h-10v10"/></svg></div>
        <div><h4>Roof Coatings:</h4><p>Extend the lifespan of existing roofs and reduce maintenance costs.</p></div>
      </div>
      <div class="photo" role="img" aria-label="Roofer working on a dark shingled roof" style="left:330px;top:620px;width:240px;height:115px;background:linear-gradient(160deg,rgba(255,255,255,0) 20%,#8a8f99 55%,#5d626b)"></div>
    </div>

    <!-- inside page 2 -->
    <div class="page page--right in2">
      <svg class="bg" width="570" height="735" viewBox="0 0 570 735">
        <defs>
          <linearGradient id="svcBlue" x1="0" y1="0" x2="1" y2="1">
            <stop offset="0" stop-color="#2a3795"/><stop offset="1" stop-color="#2f44b0"/>
          </linearGradient>
        </defs>
        <polygon points="0,0 570,0 570,150 520,165 0,165" fill="url(#svcBlue)"/>
        <polygon points="430,0 570,0 570,150" fill="#1f62d8" opacity=".5"/>
        <circle cx="404" cy="103" r="7" fill="none" stroke="#fff" stroke-width="1"/>
        <line x1="320" y1="28" x2="350" y2="58" stroke="#fff" stroke-width="1.2" opacity=".7"/>
        <line x1="330" y1="22" x2="360" y2="52" stroke="#fff" stroke-width="1.2" opacity=".7"/>
      </svg>
      <div class="abs sec-tag" style="left:25px;top:26px">OUR <b>SERVICES</b></div>
      <p class="abs services-intro">We offer comprehensive roofing solutions for every stage of your roof’s lifecycle.</p>
      <div class="abs frame" style="left:25px;top:130px;width:245px;height:170px">
        <div class="inner">
          <div class="photo" role="img" aria-label="Gloved hands repairing roof shingles" style="inset:0;background:linear-gradient(160deg,#6d6a66,#3d3b3a 50%,#8a8a88)"></div>
        </div>
      </div>
      <div class="abs frame" style="left:290px;top:130px;width:255px;height:170px">
        <div class="inner">
          <div class="photo" role="img" aria-label="Grey two-storey house with white garage doors" style="inset:0;background:linear-gradient(180deg,#c7d3e0,#5b6675 50%,#c9ccd0)"></div>
        </div>
      </div>

      <div class="item" style="left:25px;top:335px">
        <div class="icon"><svg viewBox="0 0 34 34"><path d="M4 28L10 12h14l6 16z"/><path d="M8 20h18M6 24h22"/><circle cx="24" cy="10" r="5"/></svg></div>
        <div><h4>ROOF REPAIRS:</h4><p>Fast, reliable fixes to extend roof life.</p></div>
      </div>
      <div class="item" style="left:295px;top:335px">
        <div class="icon"><svg viewBox="0 0 34 34"><path d="M4 28L17 14l13 14"/><path d="M12 13l4 4 8-9"/><path d="M4 28h26"/></svg></div>
        <div><h4>PREVENTATIVE<br>MAINTENANCE:</h4><p>Keep your roof in optimal condition year-round.</p></div>
      </div>
      <div class="divider" style="left:25px;top:425px;width:245px"></div>
      <div class="divider" style="left:295px;top:425px;width:250px"></div>
      <div class="item" style="left:25px;top:448px">
        <div class="icon"><svg viewBox="0 0 34 34"><path d="M4 28V12h18v16M4 18h18M4 23h18M12 12v16"/><circle cx="24" cy="22" r="5"/><path d="M28 26l4 4"/></svg></div>
        <div><h4>ROOF INSPECTIONS:</h4><p>Thorough assessments to identify potential issues.</p></div>
      </div>
      <div class="item" style="left:295px;top:448px">
        <div class="icon"><svg viewBox="0 0 34 34"><path d="M4 16L17 5l13 11M8 13v16h18V13"/><path d="M17 12v10M13 18l4 4 4-4"/></svg></div>
        <div><h4>NEW ROOF<br>INSTALLATIONS:</h4><p>High-quality installations with certified materials.</p></div>
      </div>
      <div class="divider" style="left:25px;top:532px;width:245px"></div>
      <div class="divider" style="left:295px;top:532px;width:250px"></div>
      <div class="photo" role="img" aria-label="Roofer installing shingles on a large roof" style="left:250px;top:520px;width:320px;height:215px;background:linear-gradient(160deg,rgba(255,255,255,0) 15%,#c9ccd3 45%,#7c818c)"></div>
      <div class="item" style="left:25px;top:555px">
        <div class="icon"><svg viewBox="0 0 34 34"><path d="M6 8l4-2 3 6-3 2c1 3 3 6 6 8l2-3 6 3-2 4C13 26 6 18 6 8z"/><path d="M20 5h6l-6 8h6"/></svg></div>
        <div><h4>EMERGENCY<br>SERVICES:</h4><p>24/7 rapid response to urgent roofing issues.</p></div>
      </div>
      <div class="abs" style="left:25px;top:708px;width:370px;height:2px;background:var(--red)"></div>
      <p class="abs url-foot">www.brackenvaleroofing.com</p>
    </div>
  </section>

</div>
</body>
</html>
```